Business card design needed

Family General Practitioner/ Family Physician.
Logo is the logo of the Noble Guild of Family Healers Oceania
http://kpltw.varendo.example/ImageShelf/marks/pages/NGFHO%20mark_jpg.htm
Updates

Project Deadline Extended
Reason: Just a bit more time to make changes and the weekend for me to look at things closely and to choose. Thanks, Orin

Thanks for all the submissions. So many of them are really works of art. Not one of them are not good. The ones that I am eliminating are the ones that I think are not suitable for me personally only, and because if I don't, it makes it very difficult to decide as many of you are also sending me slight variations of a card. I have just decided to choose a second place card too. Can't thank you all enough. Good luck, Orin. P.S - Working today till 10 pm as the card says :-), so probably won't be able to give a feedback till late Saturday night or Sunday morning here in Sydney, Australia. 

Project Deadline Extended
Reason: Just added a second place to the budget and realised that Australia is ahead of the rest of the world in the time zone (only :-) - don't want to offend anyone or start a debate!! ) , so Monday deadline will mean it will be a weekend for the rest of the world. Just wanted to give everyone more time to submit their best, especially since I will be picking a second card too. Can't thank everyone enough for the submissions. P.S - Not keen on photos on the card.

Industry/Entity Type

Business

Contact Information for Business Card

Dr. Orin Halvey M.B.B.S., F.N.G.F.H.O
Family General Practitioner
Address, timings, phone and fax number on the back.

Requirements
Must have
• Timings
Mon 7 am - 7 pm
Tues 7 am - 12 pm
Wed 7 am - 10 pm
Thurs 7 am - 12 pm
Fri 7 am - 8 pm
Sat 8 am - 10 pm
Sun - Off

```html
<!DOCTYPE html>
<html lang="en">
<head>
<meta charset="utf-8">
<title>Dr. Orin Halvey – Business Card</title>
<link rel="stylesheet" href="https://fonts.googleapis.com/css2?family=Montserrat:wght@500;600&display=swap">
<style>
  :root {
    --backdrop: #eef1f4;
    --card-white: #ffffff;
    --card-blue: #4599c6;
    --ink-blue: #3a86b3;
    --text-white: #ffffff;
  }
  html, body {
    margin: 0;
    padding: 0;
    width: 1200px;
    height: 797px;
    overflow: hidden;
    background: var(--backdrop);
  }
  .canvas {
    position: relative;
    width: 1200px;
    height: 797px;
    display: flex;
    align-items: center;
    justify-content: center;
  }
  .card {
    position: relative;
    width: 1080px;
    height: 704px;
    background: var(--card-white);
    overflow: hidden;
    box-shadow: 0 2px 10px rgba(0, 0, 0, 0.12);
    font-family: "Montserrat", sans-serif;
  }
  .card-band {
    position: absolute;
    inset: 0;
    width: 100%;
    height: 100%;
  }
  .guild-mark {
    position: absolute;
    left: 60px;
    top: 42px;
    display: flex;
    align-items: flex-start;
    gap: 14px;
    color: var(--ink-blue);
    font-weight: 600;
    font-size: 20px;
    line-height: 1.25;
    letter-spacing: 0.04em;
    font-variant: small-caps;
    max-width: 300px;
  }
  .guild-mark__square {
    flex: 0 0 auto;
    width: 22px;
    height: 22px;
    margin-top: 2px;
    background: var(--ink-blue);
  }
  .identity {
    position: absolute;
    left: 553px;
    top: 500px;
    color: var(--text-white);
    font-variant: small-caps;
  }
  .identity__name {
    margin: 0;
    font-size: 46px;
    font-weight: 600;
    letter-spacing: 0.08em;
    line-height: 1;
  }
  .identity__credentials {
    margin: 20px 0 0;
    font-size: 24px;
    font-weight: 600;
    letter-spacing: 0.12em;
    line-height: 1;
  }
  .identity__role {
    margin: 22px 0 0;
    font-size: 24px;
    font-weight: 600;
    letter-spacing: 0.1em;
    line-height: 1;
  }
</style>
</head>
<body>
  <main class="canvas">
    <section class="card" aria-label="Business card of Dr. Orin Halvey">
      <svg class="card-band" viewBox="0 0 1080 704" aria-hidden="true">
        <polygon points="0,279 1080,150 1080,704 0,704" fill="var(--card-blue)"/>
      </svg>

      <div class="guild-mark">
        <span class="guild-mark__square"></span>
        <span class="guild-mark__name">Noble Guild of Family Healers Oceania</span>
      </div>

      <div class="identity">
        <h1 class="identity__name">Dr. Orin Halvey</h1>
        <p class="identity__credentials">M.B.B.S., F.N.G.F.H.O</p>
        <p class="identity__role">Family General Practitioner</p>
      </div>
    </section>
  </main>
</body>
</html>
```